Business Card Design For A Renovation Contractor Company

We need a business card for a new company based in Singapore, our company name is "RB Tolvane". We are a renovation contractor that builds designs into reality. We build more of F&B restaurants, retail stores and commercial offices. We work very closely with designers. The final design should communicate to our client that we are a company that you can trust, that will plan and complete your project without giving you a headache. I like my client to remember my company as "RB". The beauty of SIMPLE is important.

Industry/Entity Type

Contractor

Requirements
Nice to have
• Black or Red base

```html
<!DOCTYPE html>
<html lang="en">
<head>
<meta charset="utf-8">
<title>RB Tolvane — Business Card</title>
<link rel="stylesheet" href="https://fonts.googleapis.com/css2?family=Arimo:wght@400;700&family=Jost:wght@400;500&display=swap">
<style>
  :root {
    --backdrop: #e9e6e2;
    --card: #ffffff;
    --ink: #1a1a1a;
    --ink-soft: #4a4a4a;
    --red: #e0201f;
    --rule: #b9b9b9;
    --shadow: rgba(0, 0, 0, 0.18);
  }
  * { box-sizing: border-box; margin: 0; padding: 0; }
  html, body {
    width: 1200px; height: 720px; overflow: hidden;
    background: var(--backdrop);
  }
  .stage {
    width: 1200px; height: 720px;
    display: flex; align-items: center; justify-content: center; gap: 60px;
  }
  .card {
    width: 510px; height: 292px;
    background: var(--card);
    box-shadow: 0 6px 18px var(--shadow);
    position: relative;
    font-family: "Arimo", Arial, sans-serif;
    color: var(--ink);
  }

  /* Front */
  .brand {
    position: absolute; top: 34px; left: 0; right: 0;
    display: flex; flex-direction: column; align-items: center;
  }
  .brand-lockup { display: flex; align-items: center; gap: 12px; }
  .brand-dot {
    width: 30px; height: 30px; border-radius: 50%;
    background: var(--red);
  }
  .brand-name {
    font-family: "Jost", sans-serif; font-weight: 400;
    font-size: 44px; line-height: 1; letter-spacing: -0.5px;
    color: var(--ink);
  }
  .tagline {
    margin-top: 6px; padding-top: 3px;
    border-top: 2px solid var(--ink);
    font-size: 15px; letter-spacing: 0.3px; color: var(--ink-soft);
    width: 250px; text-align: center;
  }
  .details {
    position: absolute; top: 150px; left: 0; right: 0;
    display: flex; justify-content: center;
  }
  .person {
    text-align: right; padding-right: 18px;
    border-right: 1px solid var(--rule);
    width: 230px;
  }
  .person-name { font-weight: 700; font-size: 19px; color: var(--red); }
  .person-title { font-size: 13px; color: var(--ink-soft); margin-top: 2px; }
  .address { font-size: 14px; color: var(--ink-soft); margin-top: 12px; line-height: 1.4; }
  .contact {
    list-style: none; padding-left: 18px;
    font-size: 13.5px; color: var(--ink-soft); line-height: 1.55;
    width: 230px;
  }
  .contact-label { color: var(--red); }

  /* Back */
  .card-back .mark {
    position: absolute; top: 92px; left: 0; right: 0;
    display: flex; justify-content: center; align-items: center; gap: 18px;
  }
  .card-back .brand-dot { width: 48px; height: 48px; }
  .card-back .brand-name { font-size: 58px; }
  .web {
    position: absolute; right: 34px; bottom: 32px;
    font-family: "Jost", sans-serif; font-size: 19px; letter-spacing: 3px;
    color: var(--ink);
  }
  .web-accent { color: var(--red); }
</style>
</head>
<body>
<main class="stage">
  <section class="card card-front" aria-label="Business card front">
    <div class="brand">
      <div class="brand-lockup">
        <span class="brand-dot"></span>
        <span class="brand-name">RB Tolvane</span>
      </div>
      <p class="tagline">turning plans into places</p>
    </div>
    <div class="details">
      <div class="person">
        <p class="person-name">Your Name</p>
        <p class="person-title">Title</p>
        <p class="address">Door No. Street Name<br>City Name, State, Zip Code</p>
      </div>
      <ul class="contact">
        <li><span class="contact-label">p:</span> 123-456-7890</li>
        <li><span class="contact-label">c:</span> 123-456-7890</li>
        <li><span class="contact-label">e:</span> info@rbtolvane.com</li>
        <li><span class="contact-label">w:</span> www.rbtolvane.com</li>
      </ul>
    </div>
  </section>

  <section class="card card-back" aria-label="Business card back">
    <div class="mark">
      <span class="brand-dot"></span>
      <span class="brand-name">RB Tolvane</span>
    </div>
    <p class="web">www.rb<span class="web-accent">tolvane</span>.com</p>
  </section>
</main>
</body>
</html>
```